My name is Delia Okonkwo,I want to create a web page for my personal dog grooming business. The name on the web page can be "Delia's Dog Grooming" I am located in San Antonio Texas. The page would help grow my customer base. Before and after pictures would display the quality of work that I do. On my page I can provide information about myself, my services, and pricing.
Updates

I have updated project to guaranteed pay

Please try to incorporate a schnauzer in an icon or logo. My dog is a schnauzer. THANKS!!!!!!!!!!!!

Target Market(s)

Dog Owners

Industry/Entity Type

Business

Requirements
Must have
• -A spot for before and after pictures.
-An about me section
-A section to make an appointment
Nice to have
• My favorite Color is purple. I think different shades of purple would be nice or purple with a light green

please incorporate a schnauzer in any icon or logo. My dog is a schnauzer.

```html
<!DOCTYPE html>
<html lang="en">
<head>
<meta charset="utf-8">
<title>Delia's Dog Grooming</title>
<link rel="stylesheet" href="https://fonts.googleapis.com/css2?family=Oswald:wght@600;700&family=Open+Sans:wght@400;600&display=swap">
<style>
:root{
  --lilac-top:#dcb0e2;
  --lilac-mid:#c27ad0;
  --purple-deep:#9438b0;
  --purple-dark:#6e1f86;
  --nav-band:#a54bbb;
  --tab:#cf86dc;
  --panel:rgba(255,255,255,.72);
  --heading-dark:#6c2a7e;
  --body-text:#3d2d42;
  --white:#ffffff;
  --slide-title:#c77fd2;
  --slide-sub:#7b6f7f;
  --green:#7a9a2a;
  --btn-green:#7fcc12;
  --btn-green-dark:#5a9a06;
  --ribbon:#8fbf3a;
  --footer:#a04fb8;
}
*{box-sizing:border-box;margin:0;padding:0}
html,body{width:1200px;height:1150px;overflow:hidden}
body{
  position:relative;
  font-family:"Open Sans",Arial,sans-serif;
  background:linear-gradient(180deg,var(--lilac-top) 0%,#d49ad9 25%,var(--lilac-mid) 60%,var(--purple-deep) 92%);
  color:var(--body-text);
}
.swoosh{position:absolute;left:0;top:0;width:1200px;height:1150px;pointer-events:none}
.brand{position:absolute;left:38px;top:28px;display:flex;align-items:center;gap:22px}
.brand-mark{width:122px;height:122px;border-radius:50%;background:#e8e8ea;border:9px solid #3a3a3a}
.brand-name{font-family:"Open Sans",Arial,sans-serif;font-weight:600;font-size:46px;line-height:50px;color:var(--white)}
.search{position:absolute;left:972px;top:92px;width:204px;height:29px;background:#fff;border:1px solid #d9c9dc;border-radius:3px;box-shadow:0 1px 3px rgba(0,0,0,.2);font-size:13px;color:#9a9a9a;padding:5px 12px}
.search svg{position:absolute;right:7px;top:8px}
.nav-band{position:absolute;left:0;top:168px;width:1200px;height:54px;background:linear-gradient(180deg,#b05cc5,var(--nav-band));border-top:2px solid #e6c6ec;border-bottom:2px solid #c98ed6}
.nav{position:absolute;top:168px;left:0;width:1200px;height:60px;list-style:none;font-size:16px;color:var(--white)}
.nav li{position:absolute;top:18px;transform:translateX(-50%)}
.nav .home{top:0;left:549px;width:78px;height:62px;background:var(--tab);border-radius:0 0 4px 4px;box-shadow:0 3px 5px rgba(0,0,0,.25);color:#2a1a2e;text-align:center;padding-top:18px}
.panel-about{position:absolute;left:18px;top:266px;width:450px;height:330px;background:var(--panel);padding:14px 22px 0 22px}
.h-about{font-family:"Oswald",sans-serif;font-weight:700;font-size:24px;color:var(--heading-dark);line-height:28px}
.avatar{float:left;width:90px;height:102px;margin:12px 22px 8px 0;border:6px solid #fff;background:#c6c6c6;box-shadow:1px 2px 4px rgba(0,0,0,.35);transform:rotate(-3deg)}
.about-text{font-size:14px;line-height:19px;text-align:justify;color:var(--body-text)}
.about-text p{margin-top:12px}
.view-more{position:absolute;right:22px;bottom:8px;font-family:"Oswald",sans-serif;font-weight:700;font-size:16px;color:var(--heading-dark)}
.slider{position:absolute;left:506px;top:269px;width:648px;height:324px;background:#fff;box-shadow:0 3px 8px rgba(0,0,0,.25);padding:17px}
.slide{position:relative;width:615px;height:290px;background:linear-gradient(180deg,#f6eef7,#ecd4ef);box-shadow:inset 0 0 0 1px #ddd;overflow:hidden}
.slide-dog{position:absolute;left:35px;top:2px;width:228px;height:288px;background:linear-gradient(180deg,#8a8a8e,#c9c3b8);border-radius:40% 50% 10% 10%}
.slide-sketch{position:absolute;left:365px;top:40px;width:108px;height:88px;background:linear-gradient(180deg,#e6cfe9,#dcc0e2);border-radius:8px}
.slide-title{position:absolute;left:289px;top:142px;font-family:"Oswald",sans-serif;font-weight:700;font-size:31px;color:var(--slide-title);letter-spacing:.3px}
.slide-sub{position:absolute;left:289px;top:184px;font-family:"Oswald",sans-serif;font-weight:700;font-size:16px;color:var(--slide-sub)}
.ribbon{position:absolute;left:500px;top:262px;width:120px;height:120px;overflow:hidden}
.ribbon span{position:absolute;left:-38px;top:34px;width:170px;height:28px;background:var(--ribbon);transform:rotate(-45deg);font-family:"Oswald",sans-serif;font-weight:600;font-size:12px;color:#37520e;text-align:center;line-height:28px;box-shadow:0 2px 3px rgba(0,0,0,.3)}
.arrow{position:absolute;width:36px;height:36px;border-radius:50%;background:#3d3d3d;border:2px solid #5a5a5a}
.arrow svg{position:absolute;left:11px;top:10px}
.h-section{position:absolute;font-family:"Oswald",sans-serif;font-weight:700;font-size:30px;color:var(--white)}
.shot{position:absolute;width:132px;height:132px;border-radius:50%;border:6px solid #fff;box-shadow:0 2px 5px rgba(0,0,0,.2)}
.shot.before{background:radial-gradient(circle,#a7a3a8,#eae4ef)}
.shot.after{background:radial-gradient(circle,#8b8789,#c9d0de)}
.dash{position:absolute;width:78px;border-top:2px dashed #fff}
.label{position:absolute;font-size:14px;color:var(--white)}
.view-all{position:absolute;left:421px;top:991px;font-size:15px;color:var(--white);text-decoration:underline}
.appointment{position:absolute;left:508px;top:622px;width:648px;height:198px;background:linear-gradient(180deg,#fff,#ececec)}
.h-appt{position:absolute;left:31px;top:30px;font-family:"Oswald",sans-serif;font-weight:700;font-size:30px;color:var(--green)}
.appt-text{position:absolute;left:32px;top:76px;font-size:14px;color:#3a3a3a}
.btn{position:absolute;left:180px;top:122px;width:122px;height:40px;border-radius:5px;background:linear-gradient(180deg,#a4e02e,var(--btn-green));border:1px solid var(--btn-green-dark);font-family:Arial,sans-serif;font-weight:700;font-size:15px;color:#2d3a12;text-align:center;line-height:38px}
.appt-photo{position:absolute;right:0;top:0;width:298px;height:198px;background:linear-gradient(180deg,#eef2f5,#dde3e8)}
.services{position:absolute;left:544px;top:912px;display:grid;grid-template-columns:229px 227px 200px;row-gap:19px;list-style:none;font-size:14px;color:var(--white)}
.services li{padding-left:20px;position:relative;line-height:19px}
.services li::before{content:"";position:absolute;left:3px;top:6px;width:8px;height:8px;border-radius:50%;background:#fff}
.footer{position:absolute;left:0;top:1053px;width:1200px;height:97px;background:var(--footer);border-top:3px solid var(--purple-dark)}
.copyright{position:absolute;left:22px;top:37px;font-size:13px;color:var(--white)}
.social{position:absolute;top:28px;right:32px;display:flex;gap:9px;list-style:none}
.social li{width:35px;height:35px;border-radius:50%;background:#fff;box-shadow:0 1px 3px rgba(0,0,0,.3)}
</style>
</head>
<body>
<svg class="swoosh" viewBox="0 0 1200 1150" aria-hidden="true">
  <path d="M0 520 C120 700 180 900 330 1053 L0 1053 Z" fill="#ffffff" opacity=".08"/>
  <path d="M60 1053 C10 900 40 700 260 580" fill="none" stroke="#fff" stroke-opacity=".18" stroke-width="3"/>
  <path d="M700 0 C850 80 1050 60 1200 10" fill="none" stroke="#fff" stroke-opacity=".3" stroke-width="2"/>
  <path d="M900 0 C1000 40 1120 40 1200 30 L1200 0 Z" fill="#fff" opacity=".12"/>
  <path d="M320 560 C420 650 700 600 1200 760" fill="none" stroke="#fff" stroke-opacity=".12" stroke-width="2"/>
</svg>

<header>
  <div class="brand">
    <div class="brand-mark" role="img" aria-label="Round brand badge"></div>
    <div class="brand-name">Delia's<br>Dog Grooming</div>
  </div>
  <div class="search">Search
    <svg width="12" height="12" viewBox="0 0 12 12" aria-hidden="true"><circle cx="5" cy="5" r="3.5" fill="none" stroke="#aaa" stroke-width="1.5"/><line x1="7.5" y1="7.5" x2="11" y2="11" stroke="#aaa" stroke-width="1.5"/></svg>
  </div>
</header>

<div class="nav-band"></div>
<ul class="nav">
  <li class="home">Home</li>
  <li style="left:674px">About Us</li>
  <li style="left:802px">Gallery</li>
  <li style="left:942px">Testimonials</li>
  <li style="left:1094px">Contact Us</li>
</ul>

<section class="panel-about">
  <h2 class="h-about">ABOUT ME</h2>
  <div class="about-text">
    <div class="avatar" role="img" aria-label="Portrait photo of the groomer"></div>
    <p style="margin-top:14px">Duis aute irure dolor in reprehenderit in voluptate velit esse cillum dolore eu fugiat nulla pariatur. Excepteur sint occaecat cupidatat non proident, sunt in culpa qui officia deserunt mollit.</p>
    <p style="clear:both;padding-top:4px">Neque porro quisquam est, qui dolorem ipsum quia dolor sit amet, consectetur, adipisci velit, sed quia non numquam eius modi tempora incidunt ut labore et dolore magnam aliquam quaerat voluptatem. Ut enim ad minima veniam, quis nostrum exercitationem ullam corporis suscipit laboriosam, nisi ut aliquid ex ea commodi consequatur Quis autem vel eum iure reprehenderit molestiae.</p>
  </div>
  <span class="view-more">VIEW MORE</span>
</section>

<section class="slider">
  <div class="slide">
    <div class="slide-dog" role="img" aria-label="Photo of a groomed schnauzer"></div>
    <div class="slide-sketch" role="img" aria-label="Small schnauzer illustration"></div>
    <div class="slide-title">EXERCITATION ULLAMCO</div>
    <div class="slide-sub">LABORIS NISI UT ALIQUIP EX EA COMMODO</div>
  </div>
</section>
<div class="ribbon"><span>TESTIMONIALS</span></div>
<div class="arrow" style="left:480px;top:412px"><svg width="12" height="14" viewBox="0 0 12 14" aria-hidden="true"><path d="M8 2 L3 7 L8 12" fill="none" stroke="#fff" stroke-width="2.5"/></svg></div>
<div class="arrow" style="left:1144px;top:412px"><svg width="12" height="14" viewBox="0 0 12 14" aria-hidden="true"><path d="M4 2 L9 7 L4 12" fill="none" stroke="#fff" stroke-width="2.5"/></svg></div>

<h2 class="h-section" style="left:18px;top:615px">OUR GROOMINGS</h2>
<span class="label" style="left:28px;top:746px">Before</span>
<div class="shot before" style="left:80px;top:684px" role="img" aria-label="Dog before grooming"></div>
<div class="dash" style="left:215px;top:755px"></div>
<div class="shot after" style="left:296px;top:684px" role="img" aria-label="Dog after grooming"></div>
<span class="label" style="left:440px;top:746px">After</span>
<span class="label" style="left:28px;top:903px">Before</span>
<div class="shot before" style="left:80px;top:842px" role="img" aria-label="Dog before grooming"></div>
<div class="dash" style="left:215px;top:911px"></div>
<div class="shot after" style="left:296px;top:842px" role="img" aria-label="Dog after grooming"></div>
<span class="label" style="left:440px;top:903px">After</span>
<a class="view-all">View all</a>

<section class="appointment">
  <h2 class="h-appt">MAKE AN APOINTMENT</h2>
  <p class="appt-text">Excepteur sint occaecat cupidatat non proident,</p>
  <div class="btn">Click Here</div>
  <div class="appt-photo" role="img" aria-label="Schnauzer sitting beside a basket of red flowers"></div>
</section>

<h2 class="h-section" style="left:540px;top:836px">OUR SERVICES</h2>
<ul class="services">
  <li>Quis autem vel</li><li>Quis autem vel</li><li>Quis autem vel</li>
  <li>Voluptatem sequi</li><li>Voluptatem sequi</li><li>Voluptatem sequi</li>
  <li>Neque porroquisquam</li><li>Neque porroquisquam</li><li>Nemo enimipsam</li>
</ul>

<footer class="footer">
  <p class="copyright">Copyright © 2012 www.DeliasGroomingParlor.com&nbsp; All rights reserved</p>
  <ul class="social" aria-label="Social links">
    <li></li><li></li><li></li><li></li><li></li>
  </ul>
</footer>
</body>
</html>
```